Help design website for "Brightwater Civic Advisors" to advance the common good

Here is the Google doc link that lays out the design:

https://files.plumrivet.example/sheet/d/7QmTzR2wLx9KpVbN4hJcY8sEaUoFdG3iXkMnPq5rWt6/edit?usp=sharing

Here is the Google drive folder with the logos and photos: https://vault.plumrivet.example/open?id=4HkWp9LzQe2TxRvN8mBaYc3DsUoJfG6

The testimonials are being gathered and will be shared by Friday, 1/4.

The winner will also have to migrate the coding files to my hosting site.

Thank you for your help! Looking forward to seeing your designs.

Target Market(s)

Prospective clients

Industry/Entity Type

Non Profit

Coding

Coded - Design and coding required

Number of Pages Required

5+ page

Requirements
Must have
• Noted in the Google doc regarding layout.
Nice to have

```html
<!DOCTYPE html>
<html lang="en">
<head>
<meta charset="utf-8">
<title>Brightwater Civic Advisors</title>
<link href="https://fonts.googleapis.com/css2?family=Roboto+Condensed:wght@400;700&family=Poppins:wght@400;500&family=Open+Sans:wght@400;600&family=Roboto:wght@400;500&display=swap" rel="stylesheet">
<style>
:root{
  --blue:#3b8ad6;
  --navy:#0d4a8c;
  --ink:#1b1b1b;
  --text:#333;
  --muted:#666;
  --footer:#111;
  --white:#fff;
  --line:#d6d6d6;
}
*{margin:0;padding:0;box-sizing:border-box}
html,body{width:1200px;height:3309px;overflow:hidden}
body{position:relative;background:var(--white);font-family:"Open Sans",sans-serif;color:var(--text)}
.abs{position:absolute}

/* Hero */
.hero{left:0;top:0;width:1200px;height:720px;background:linear-gradient(160deg,#6b5a48 0%,#3f4c5c 45%,#2a3a4c 100%)}
.hero-photo{left:0;top:0;width:1200px;height:720px;background:radial-gradient(ellipse at 50% 35%,rgba(160,140,120,.55),rgba(30,40,55,.2) 70%)}
.nav{left:95px;top:38px;display:flex;gap:8px;font-family:"Roboto",sans-serif;font-size:16px}
.nav a{color:var(--white);text-decoration:none;padding:9px 20px;border-radius:20px}
.nav a.active{background:var(--blue)}
.brand{left:842px;top:30px;color:var(--white);font-family:"Roboto",sans-serif;font-size:17px;letter-spacing:4px;line-height:20px;text-transform:uppercase;display:flex;align-items:center;gap:12px}
.brand-mark{width:26px;height:26px;border:2px solid var(--white);border-radius:50%}
.hero-title{left:0;width:1200px;top:262px;text-align:center;color:var(--white);font-family:"Roboto Condensed",sans-serif;font-weight:700;font-size:62px;text-transform:uppercase}
.hero-sub{left:0;width:1200px;top:338px;text-align:center;color:var(--white);font-family:"Roboto Condensed",sans-serif;font-size:46px;line-height:58px}
.dots{left:1160px;top:290px;display:flex;flex-direction:column;gap:14px}
.dots span{width:7px;height:7px;border-radius:50%;background:var(--white)}
.hero-edge{left:0;top:590px;width:1200px;height:140px}

/* About */
.about-frame{left:64px;top:793px;width:397px;height:325px;border:3px solid var(--navy)}
.about-photo{left:93px;top:818px;width:435px;height:345px;background:linear-gradient(135deg,#3a3a34,#6f6656 50%,#4b4a40);box-shadow:0 6px 14px rgba(0,0,0,.25)}
.about-title{left:563px;top:820px;font-family:"Poppins",sans-serif;font-size:44px;color:var(--ink);font-weight:500}
.about-text{left:563px;top:884px;width:548px;font-size:14.5px;line-height:27.5px;color:var(--text);text-align:justify}
.btn-pill{display:inline-block;border-radius:20px;font-size:15px;text-decoration:none;text-align:center}
.about-btn{left:563px;top:1122px;width:127px;height:36px;line-height:36px;background:var(--blue);color:var(--white)}

/* Services */
.services{left:0;top:1282px;width:1200px;height:580px;background:linear-gradient(180deg,#f4f4f4 0%,#e9ecef 55%,#c9d4df 100%)}
.section-title{left:0;width:1200px;text-align:center;font-family:"Poppins",sans-serif;font-size:44px;color:var(--ink)}
.service-card{top:1495px;width:317px;height:308px;background:var(--white);border:1px solid var(--line);text-align:center}
.service-icon{top:1428px;width:124px;height:124px;border-radius:50%;display:flex;align-items:center;justify-content:center}
.service-card h3{margin-top:74px;font-family:"Open Sans",sans-serif;font-weight:600;font-size:18px;line-height:27px;color:var(--ink)}
.service-card p{margin:26px auto 0;width:250px;font-size:14px;line-height:26px;color:var(--muted)}
.service-card .btn-pill{margin-top:26px;width:115px;height:36px;line-height:33px;border:1.5px solid #555;color:var(--ink);font-size:14px}
.service-card .btn-pill.solid{background:var(--navy);border-color:var(--navy);color:var(--white)}
.arrow{top:1638px;width:34px;height:34px;border-radius:50%;background:var(--white);display:flex;align-items:center;justify-content:center}

/* Testimonial */
.testimonial{left:0;top:1860px;width:1200px;height:190px;background:var(--navy);color:var(--white);text-align:center;font-family:"Roboto",sans-serif}
.notch{left:584px;top:1842px;width:0;height:0;border-left:16px solid transparent;border-right:16px solid transparent;border-bottom:18px solid var(--navy)}
.quote{top:55px;width:1200px;font-size:15px}
.quote-by{top:90px;width:1200px;font-size:19px}
.t-dots{left:584px;top:146px;display:flex;gap:8px}
.t-dots span{width:8px;height:8px;border-radius:50%;background:#8aa9cc}
.t-dots span.on{background:var(--white)}

/* Media */
.media-card{top:2268px;width:306px;height:363px;background:var(--white);box-shadow:0 4px 16px rgba(0,0,0,.18);text-align:center}
.media-photo{width:306px;height:198px}
.media-card h3{margin-top:22px;font-family:"Open Sans",sans-serif;font-weight:600;font-size:22px;color:var(--ink)}
.media-card p{margin:10px auto 0;width:250px;font-size:13.5px;line-height:21px;color:var(--text)}
.media-card a{display:block;margin-top:10px;font-size:14px;color:var(--navy);text-decoration:none}

/* Footer */
.footer-edge{left:0;top:2735px;width:1200px;height:140px}
.footer{left:0;top:2860px;width:1200px;height:449px;background:var(--footer);color:var(--white)}
.f-col{top:76px}
.f-col h4{font-family:"Open Sans",sans-serif;font-weight:400;font-size:20px;text-transform:uppercase;margin-bottom:28px}
.f-col ul{list-style:none;font-size:15px;line-height:39px}
.contact-item{display:flex;gap:10px;margin-bottom:28px;font-size:13.5px;line-height:20px}
.contact-item b{font-weight:600;font-size:15px;text-transform:uppercase}
.field{width:258px;height:37px;background:var(--white);color:#777;font-size:15px;padding:8px 16px;margin-bottom:7px}
.send{margin-top:18px;width:126px;height:38px;background:var(--blue);color:var(--white);font-size:17px;text-align:center;line-height:38px}
.copyright{top:384px;width:1200px;text-align:center;font-size:15px;color:#ccc}
</style>
</head>
<body>

<!-- Hero -->
<div class="abs hero" role="img" aria-label="Photo of a small team working together around a laptop"></div>
<div class="abs hero-photo"></div>
<nav class="abs nav">
  <a class="active" href="#">Home</a><a href="#">About</a><a href="#">Services &amp; Testimonials</a><a href="#">Media &amp; Impact</a><a href="#">Contact</a>
</nav>
<div class="abs brand"><span class="brand-mark"></span><span>Brightwater<br>Civic Advisors</span></div>
<h1 class="abs hero-title">Brightwater Civic Advisors</h1>
<p class="abs hero-sub">Supports nonprofit organizations and<br>educational institutions</p>
<div class="abs dots"><span></span><span></span><span></span><span></span><span></span></div>
<svg class="abs hero-edge" viewBox="0 0 1200 140" preserveAspectRatio="none">
  <path d="M0 100 L600 24 L1200 100 V140 H0Z" fill="#3b8ad6"/>
  <path d="M0 122 L600 44 L1200 122 V140 H0Z" fill="#fff"/>
</svg>

<!-- About -->
<div class="abs about-frame"></div>
<div class="abs about-photo" role="img" aria-label="Portrait photo of the founder"></div>
<h2 class="abs about-title">About</h2>
<p class="abs about-text">Brightwater Civic Advisors supports nonprofit organizations and educational institutions to carry out their missions to benefit the wider community. Founder Dana Whitfield is an educator with a 22-year record of demonstrated achievement and leadership roles in nonprofits and educational institutions. Most recently, she served as Associate Dean of Students in the University and Director of the University Community Service Center at Lakeshore State University. Dana has designed, implemented, and evaluated community-based learning and leadership training programs that have attained positive</p>
<a class="abs btn-pill about-btn" href="#">Read More</a>

<!-- Services -->
<div class="abs services" role="img" aria-label="Soft background photo of a professional in a city office"></div>
<h2 class="abs section-title" style="top:1318px">Our Services</h2>

<div class="abs arrow" style="left:45px"><svg width="12" height="14" viewBox="0 0 12 14"><path d="M8 2 L3 7 L8 12" fill="none" stroke="#555" stroke-width="1.6"/></svg></div>
<div class="abs arrow" style="left:1125px"><svg width="12" height="14" viewBox="0 0 12 14"><path d="M4 2 L9 7 L4 12" fill="none" stroke="#555" stroke-width="1.6"/></svg></div>

<div class="abs service-card" style="left:98px">
  <h3>Staff Professional<br>Development</h3>
  <p>It is a long established fact that a reader will be distracted by the readable content of a page</p>
  <a class="btn-pill" href="#">Read more</a>
</div>
<div class="abs service-card" style="left:445px">
  <h3>Community Partnership<br>Development</h3>
  <p>It is a long established fact that a reader will be distracted by the readable content of a page</p>
  <a class="btn-pill solid" href="#">Read more</a>
</div>
<div class="abs service-card" style="left:793px">
  <h3>Group Facilitation &amp;<br>Leadership Training</h3>
  <p>It is a long established fact that a reader will be distracted by the readable content of a page</p>
  <a class="btn-pill" href="#">Read more</a>
</div>

<div class="abs service-icon" style="left:195px;background:var(--blue)">
  <svg width="70" height="64" viewBox="0 0 70 64" fill="none" stroke="#fff" stroke-width="2.2">
    <circle cx="35" cy="16" r="8"/><path d="M22 46 V34 a13 12 0 0 1 26 0 V46"/>
    <circle cx="14" cy="22" r="6"/><path d="M4 48 V38 a10 9 0 0 1 14-8"/>
    <circle cx="56" cy="22" r="6"/><path d="M66 48 V38 a10 9 0 0 0 -14-8"/>
    <path d="M2 56 H68"/>
  </svg>
</div>
<div class="abs service-icon" style="left:542px;background:var(--navy)">
  <svg width="70" height="60" viewBox="0 0 70 60" fill="none" stroke="#fff" stroke-width="2.2">
    <rect x="10" y="6" width="50" height="34" rx="2"/><path d="M2 48 H68 L62 54 H8Z"/>
    <path d="M28 18 L22 23 L28 28 M42 18 L48 23 L42 28 M37 15 L33 31"/>
  </svg>
</div>
<div class="abs service-icon" style="left:890px;background:var(--blue)">
  <svg width="64" height="66" viewBox="0 0 64 66" fill="none" stroke="#fff" stroke-width="2.2">
    <rect x="10" y="8" width="36" height="50" rx="2"/><path d="M17 20 H39 M17 28 H39 M17 36 H33 M17 44 H30"/>
    <path d="M52 6 V44 L56 52 L60 44 V6Z"/>
  </svg>
</div>

<!-- Testimonial -->
<div class="abs notch"></div>
<section class="abs testimonial">
  <p class="abs quote">“ It is a long established fact that a reader will be distracted by the readable content of a page when looking at its layout. ”</p>
  <p class="abs quote-by">Marisol Ortega, Executive Director, Riverbend Community Development</p>
  <div class="abs t-dots"><span></span><span class="on"></span></div>
</section>

<!-- Media -->
<h2 class="abs section-title" style="top:2146px">Media &amp; Impact</h2>
<article class="abs media-card" style="left:112px">
  <div class="media-photo" role="img" aria-label="Photo of a workshop audience seated at round tables" style="background:linear-gradient(135deg,#4a3a30,#8a6f58 50%,#3a2e28)"></div>
  <h3>Articles</h3>
  <p>The point of using Lorem Ipsum is that it has a more-or-less normal</p>
  <a href="#">View More »</a>
</article>
<article class="abs media-card" style="left:455px">
  <div class="media-photo" role="img" aria-label="Photo of a community group gathered outdoors" style="background:linear-gradient(135deg,#4d5a3c,#8c8a72 50%,#3c4634)"></div>
  <h3>Videos</h3>
  <p>The point of using Lorem Ipsum is that it has a more-or-less normal</p>
  <a href="#">View More »</a>
</article>
<article class="abs media-card" style="left:799px">
  <div class="media-photo" role="img" aria-label="Photo of a speaker at a podium on a dark stage" style="background:linear-gradient(135deg,#1a1410,#4a3a32 55%,#120e0c)"></div>
  <h3>Podcasts</h3>
  <p>The point of using Lorem Ipsum is that it has a more-or-less normal</p>
  <a href="#">View More »</a>
</article>

<!-- Footer -->
<svg class="abs footer-edge" viewBox="0 0 1200 140" preserveAspectRatio="none">
  <path d="M0 95 L600 14 L1200 95 V140 H0Z" fill="#3b8ad6"/>
  <path d="M0 115 L600 34 L1200 115 V140 H0Z" fill="#111"/>
</svg>
<footer class="abs footer">
  <div class="abs f-col" style="left:115px">
    <h4>Contact Us</h4>
    <div class="contact-item">
      <svg width="20" height="16" viewBox="0 0 20 16" fill="none" stroke="#fff" stroke-width="1.5"><rect x="1" y="2" width="18" height="12"/><path d="M1 2 L10 9 L19 2"/></svg>
      <div><b>Email Address</b><br>info@brightwatercivic.example</div>
    </div>
    <div class="contact-item">
      <svg width="20" height="20" viewBox="0 0 20 20" fill="none" stroke="#fff" stroke-width="1.5"><path d="M4 2 L8 2 L9 6 L6.5 8 a11 11 0 0 0 5.5 5.5 L14 11 L18 12 L18 16 a2 2 0 0 1 -2 2 A15 15 0 0 1 2 4 a2 2 0 0 1 2-2Z"/></svg>
      <div><b>Phone Number</b><br>555-014-2290</div>
    </div>
  </div>
  <div class="abs f-col" style="left:408px">
    <h4>About</h4>
    <ul><li>Home</li><li>About Us</li><li>Services</li><li>Testimonials</li></ul>
  </div>
  <div class="abs f-col" style="left:623px">
    <h4>Resources</h4>
    <ul><li>Articles</li><li>Videos</li><li>Podcasts</li><li>Contact</li></ul>
  </div>
  <div class="abs f-col" style="left:848px">
    <h4>Get in Touch</h4>
    <div class="field" style="margin-left:4px">Your Name</div>
    <div class="field" style="margin-left:4px">Email address</div>
    <div class="field" style="margin-left:4px">Phone</div>
    <div class="send" style="margin-left:4px">SEND</div>
  </div>
  <p class="abs copyright">© 2019 Company Name &nbsp;All right reserved</p>
</footer>

</body>
</html>
```